IT Company requires new Business Card design.

Over the years we have had a few different business card designs. We are now due for new cards across the board for all staff. We felt this would be a good time to start fresh with a new design. Our traditional card simply had our details on the front, and a list of services on the back. We don't particularly need the list of services, we have had cards where the only thing on the rear of the card was our logo.
Feel free to be creative, we would like our tag line "Complete IT Management" to appear at some point, doesn't necessarily have to be with the logo.
I have attached samples and drafts of various previous cards we have used over the years.

```html
<!DOCTYPE html>
<html lang="en">
<head>
<meta charset="utf-8">
<title>Calder Systems – Business Cards</title>
<link href="https://fonts.googleapis.com/css2?family=Open+Sans:wght@400;600;700&display=swap" rel="stylesheet">
<style>
  :root {
    --slate: #5f7383;
    --slate-dark: #46545f;
    --slate-soft: #6c808f;
    --paper: #ffffff;
    --ink-light: #e8edf1;
    --backdrop: #e7e4df;
  }
  * { box-sizing: border-box; margin: 0; padding: 0; }
  html, body {
    width: 1200px; height: 720px; overflow: hidden;
    background: var(--backdrop);
    font-family: "Open Sans", Arial, sans-serif;
  }
  .canvas {
    position: relative; width: 1200px; height: 720px;
  }
  .card {
    position: absolute; top: 205px;
    width: 540px; height: 310px;
    background: var(--paper);
    box-shadow: 0 2px 6px rgba(0,0,0,0.12);
    overflow: hidden;
  }
  .card--details { left: 40px; }
  .card--brand { left: 620px; }

  /* brand lockup */
  .brand { display: flex; align-items: center; gap: 14px; color: var(--slate); }
  .brand__square { background: var(--slate); flex: none; }
  .brand__name {
    font-weight: 700; text-transform: uppercase; line-height: 0.92;
    letter-spacing: 0.5px;
  }

  /* details side */
  .card--details .brand { position: absolute; left: 120px; top: 38px; }
  .card--details .brand__square { width: 62px; height: 62px; }
  .card--details .brand__name { font-size: 34px; }
  .details-band {
    position: absolute; left: 0; right: 0; top: 128px; bottom: 0;
    background: var(--slate);
    color: var(--ink-light);
  }
  .details-band__mark {
    position: absolute; right: 70px; top: 18px;
    width: 84px; height: 84px;
    background: var(--slate-soft);
  }
  .address {
    position: absolute; left: 150px; top: 14px;
    font-size: 13px; color: var(--paper);
  }
  .person {
    position: absolute; left: 36px; top: 58px;
    font-size: 16px; color: var(--paper);
  }
  .person__name { font-weight: 700; }
  .person__role { font-weight: 400; font-size: 14px; }
  .person__mobile { font-size: 14px; margin-left: 10px; }
  .contact-list {
    position: absolute; left: 36px; top: 86px;
    list-style: none; font-size: 13.5px; line-height: 21px; color: var(--paper);
  }
  .contact-list li { display: flex; align-items: center; gap: 9px; }
  .contact-list svg { width: 13px; height: 13px; flex: none; }

  /* brand side */
  .card--brand .brand { position: absolute; left: 112px; top: 86px; gap: 18px; }
  .card--brand .brand__square { width: 96px; height: 96px; }
  .card--brand .brand__name { font-size: 44px; }
  .tagline {
    display: block; margin-top: 8px;
    font-size: 12px; font-weight: 400; letter-spacing: 3px;
    text-transform: uppercase; color: var(--slate-dark);
  }
  .website {
    position: absolute; left: 0; right: 0; bottom: 40px;
    text-align: center; font-size: 17px; font-weight: 600;
    letter-spacing: 1.5px; color: var(--slate-dark);
  }
</style>
</head>
<body>
<main class="canvas">

  <section class="card card--details" aria-label="Business card, details side">
    <div class="brand">
      <span class="brand__square"></span>
      <span class="brand__name">Calder<br>Systems</span>
    </div>
    <div class="details-band">
      <span class="details-band__mark"></span>
      <p class="address">Suite 4, 22 Marlow Street, Hillcrest WA 6100</p>
      <p class="person">
        <span class="person__name">Daniel Reeve,</span>
        <span class="person__role">Operation Manager</span>
      </p>
      <ul class="contact-list">
        <li>
          <svg viewBox="0 0 16 16" aria-hidden="true"><circle cx="8" cy="8" r="7.5" fill="none" stroke="#fff"/><path d="M5 4.5l1.5-.5 1 2-1 .8a5 5 0 0 0 2.7 2.7l.8-1 2 1-.5 1.5c-3.2.2-6.7-3.3-6.5-6.5z" fill="#fff"/></svg>
          08 5550 1234
          <span class="person__mobile">
            <svg viewBox="0 0 16 16" aria-hidden="true" style="vertical-align:-2px"><rect x="4.5" y="1.5" width="7" height="13" rx="1.5" fill="none" stroke="#fff"/><circle cx="8" cy="12" r="0.9" fill="#fff"/></svg>
            0400 555 018
          </span>
        </li>
        <li>
          <svg viewBox="0 0 16 16" aria-hidden="true"><circle cx="8" cy="5" r="3" fill="#fff"/><path d="M2.5 15c0-3.5 2.5-5.5 5.5-5.5s5.5 2 5.5 5.5z" fill="#fff"/></svg>
          08 5550 1235
        </li>
        <li>
          <svg viewBox="0 0 16 16" aria-hidden="true"><rect x="1.5" y="3.5" width="13" height="9" fill="none" stroke="#fff"/><path d="M1.5 3.5L8 9l6.5-5.5" fill="none" stroke="#fff"/></svg>
          daniel@caldersystems.com.au
        </li>
        <li>
          <svg viewBox="0 0 16 16" aria-hidden="true"><circle cx="8" cy="8" r="6.5" fill="none" stroke="#fff"/><ellipse cx="8" cy="8" rx="3" ry="6.5" fill="none" stroke="#fff"/><path d="M1.5 8h13" stroke="#fff"/></svg>
          www.caldersystems.com.au
        </li>
      </ul>
    </div>
  </section>

  <section class="card card--brand" aria-label="Business card, brand side">
    <div class="brand">
      <span class="brand__square"></span>
      <span class="brand__name">Calder<br>Systems<span class="tagline">Complete IT Management</span></span>
    </div>
    <p class="website">www.caldersystems.com.au</p>
  </section>

</main>
</body>
</html>
```